Corvane Capital Business Cards

These are professional business cards that are for my family office.
Put fake emails and phone numbers as of now until I finalize those components. This family office controls my families investments, assets, and future. The cards should be professional.
..
.
.
.
I just uploaded another variation of a logo I would like to see as a business card to I am inbeteen which logo to use

Target Market(s)

business

Industry/Entity Type

business

Contact Information for Business Card

Professional, wealth related, finance related.

Requirements
Must have
• Logo

```html
<!DOCTYPE html>
<html lang="en">
<head>
<meta charset="utf-8">
<title>Corvane Capital Business Cards</title>
<link rel="stylesheet" href="https://fonts.googleapis.com/css2?family=Bodoni+Moda:wght@500;600&family=Arimo:wght@400&display=swap">
<style>
  :root {
    --backdrop: #161616;
    --card: #2a2a2a;
    --ink-light: #f4f2ee;
    --gold: #c4a76c;
    --serif: "Bodoni Moda", "Didot", serif;
    --sans: "Arimo", "Helvetica Neue", Arial, sans-serif;
  }
  * { box-sizing: border-box; margin: 0; padding: 0; }
  html, body {
    width: 1200px;
    height: 900px;
    overflow: hidden;
    background: var(--backdrop);
  }
  .sheet {
    position: relative;
    width: 1200px;
    height: 900px;
  }
  .card {
    position: absolute;
    width: 560px;
    height: 320px;
    background: var(--card);
    border-radius: 16px;
    box-shadow: 0 18px 40px rgba(0, 0, 0, 0.55);
  }
  .card--front { left: 110px; top: 90px; }
  .card--back  { left: 530px; top: 490px; }

  .wordmark {
    font-family: var(--serif);
    font-weight: 500;
    color: var(--ink-light);
    letter-spacing: 0.06em;
    text-transform: uppercase;
    white-space: nowrap;
  }
  .card--front .wordmark {
    position: absolute;
    left: 0; right: 0; top: 50%;
    transform: translateY(-50%);
    text-align: center;
    font-size: 40px;
  }
  .card--back .wordmark {
    position: absolute;
    left: 28px;
    width: 256px;
    top: 50%;
    transform: translateY(-50%);
    text-align: center;
    font-size: 24px;
  }
  .divider {
    position: absolute;
    left: 300px;
    top: 70px;
    width: 1px;
    height: 190px;
    background: var(--gold);
  }
  .contact {
    position: absolute;
    left: 322px;
    top: 62px;
    right: 20px;
    font-family: var(--sans);
    color: var(--ink-light);
    font-size: 12.5px;
    line-height: 1.35;
  }
  .contact__name {
    font-family: var(--serif);
    font-weight: 600;
    color: var(--gold);
    font-size: 19px;
    letter-spacing: 0.04em;
    text-transform: uppercase;
    line-height: 1.1;
  }
  .contact__role { margin-bottom: 14px; }
  .contact__address { margin-bottom: 14px; }
  .contact__list { list-style: none; }
  .contact__item {
    display: flex;
    align-items: center;
    gap: 8px;
    margin-bottom: 4px;
  }
  .contact__icon {
    width: 12px;
    height: 12px;
    flex: none;
    fill: var(--gold);
  }
</style>
</head>
<body>
<main class="sheet">
  <section class="card card--front" aria-label="Card front">
    <div class="wordmark">Corvane Capital</div>
  </section>

  <section class="card card--back" aria-label="Card back">
    <div class="wordmark">Corvane Capital</div>
    <div class="divider"></div>
    <div class="contact">
      <p class="contact__name">Daniel Reyes</p>
      <p class="contact__role">CEO/Founder</p>
      <p class="contact__address">4870 Ridgeline Ave Suite 200<br>Marlow, AB 604218</p>
      <ul class="contact__list">
        <li class="contact__item">
          <svg class="contact__icon" viewBox="0 0 12 12" aria-hidden="true"><path d="M1 4.5C1 3 3 2 6 2s5 1 5 2.5l-2 .8-.6-1.4H3.6L3 5.3zM2.5 6.5 4 5h4l1.5 1.5V10h-7z"/></svg>
          <span>(555) 014-2260</span>
        </li>
        <li class="contact__item">
          <svg class="contact__icon" viewBox="0 0 12 12" aria-hidden="true"><path d="M1 3h10v7H1zM1.8 3.6 6 6.8l4.2-3.2v.9L6 7.7 1.8 4.5z" fill-rule="evenodd"/></svg>
          <span>DanielR@corvanecapital.com</span>
        </li>
        <li class="contact__item">
          <svg class="contact__icon" viewBox="0 0 12 12" aria-hidden="true"><path d="M6 1a5 5 0 1 0 0 10A5 5 0 0 0 6 1zm0 1a4 4 0 0 1 3.4 1.9H7.2L6.5 5 5 4.3 3.6 5.2l.6 1.9 1.6.6-.3 2.2A4 4 0 0 1 6 2z"/></svg>
          <span>www.corvanecapital.com</span>
        </li>
      </ul>
    </div>
  </section>
</main>
</body>
</html>
```